Kovát Lillas Physiotherapy Business Card Vienna

We need a business card design for a newly created Physiotherapy company based in Vienna Austria.
We seek a simple, modern, minimalist design without too much color variation. The font should look young/fresh, but definitely not childish or so. Since we are a starting Business, we currently haven't got a logo, if you feel like a logo would fit your design, feel free to use one, but it's not necessary.
Target Market(s)
Healthcare, young and elderly people with mobility issues
Industry/Entity Type
Health And Wellness
Contact Information for Business Card
Name: Lilla Kovát
Title description: Physiotherapist
Phone num: +43 664 2951 4086
e-mail: lilla.praxis@bluemail.example
Colors
Designer to choose colors to be used in the design.
Requirements
Must have
- Final design language must be in German, basically, the Title Description needs to be "Physiotherapeutin" the other details remain as in the English Language.
Nice to have
- Simple, modern, minimalist design
Should not have
- too many colors, Obvious use of a skeleton, skull, spline

```html
<!DOCTYPE html>
<html lang="de">
<head>
<meta charset="utf-8">
<title>Kovát Lillas Physiotherapy – Visitenkarte</title>
<link href="https://fonts.googleapis.com/css2?family=Outfit:wght@400;600&display=swap" rel="stylesheet">
<style>
  :root {
    --backdrop: #dedede;
    --paper: #ffffff;
    --charcoal: #414143;
    --ink: #3b3b3d;
    --ink-soft: #4a4a4c;
    --on-dark: #ffffff;
  }
  * { margin: 0; padding: 0; box-sizing: border-box; }
  html, body {
    width: 1200px; height: 897px; overflow: hidden;
    background: var(--backdrop);
    font-family: "Outfit", "Century Gothic", sans-serif;
  }
  .card {
    position: absolute;
    left: 329px; width: 543px; height: 310px;
  }
  .card--front { top: 108px; background: var(--paper); color: var(--ink); }
  .card--back  { top: 479px; background: var(--charcoal); color: var(--on-dark); }

  .wordmark { position: absolute; line-height: 1; }
  .wordmark__name { display: block; font-weight: 600; letter-spacing: 0.04em; white-space: nowrap; }
  .wordmark__tag  { display: block; font-weight: 400; white-space: nowrap; }

  .card--front .wordmark { left: 27px; top: 26px; }
  .card--front .wordmark__name { font-size: 32px; }
  .card--front .wordmark__tag  { font-size: 15px; letter-spacing: 0.42em; margin-top: 3px; }

  .card--back .wordmark { left: 0; right: 0; top: 128px; text-align: center; }
  .card--back .wordmark__name { font-size: 38px; }
  .card--back .wordmark__tag  { font-size: 18px; letter-spacing: 0.44em; margin-top: 4px; padding-left: 0.44em; }

  .person {
    position: absolute; left: 29px; top: 326px;
  }
  .person { top: 222px; display: flex; align-items: baseline; white-space: nowrap; }
  .person__name { font-size: 21px; font-weight: 600; letter-spacing: 0.16em; }
  .person__divider { font-size: 21px; font-weight: 600; margin: 0 18px 0 10px; }
  .person__title { font-size: 14.5px; color: var(--ink-soft); }

  .rule {
    position: absolute; left: 27px; top: 258px;
    width: 330px; height: 1px; background: var(--ink);
  }
  .contact {
    position: absolute; left: 28px; top: 270px;
    font-size: 14.5px; color: var(--ink-soft); white-space: nowrap;
  }
  .contact__sep { margin: 0 6px; }
</style>
</head>
<body>
  <section class="card card--front">
    <div class="wordmark">
      <span class="wordmark__name">KOVÁT LILLAS</span>
      <span class="wordmark__tag">PHYSIOTHERAPY</span>
    </div>
    <div class="person">
      <span class="person__name">LILLA KOVÁT</span>
      <span class="person__divider">|</span>
      <span class="person__title">Physiotherapeutin</span>
    </div>
    <div class="rule"></div>
    <p class="contact">+43 664 2951 4086<span class="contact__sep">|</span>lilla.praxis@bluemail.example</p>
  </section>

  <section class="card card--back">
    <div class="wordmark">
      <span class="wordmark__name">KOVÁT LILLAS</span>
      <span class="wordmark__tag">PHYSIOTHERAPY</span>
    </div>
  </section>
</body>
</html>
```